Creating a Label for the Wine "Kemora"

Kemora
As you know Kemora is an imagined place or state of things in which everything is perfect. This wine reflects that. It is a high value wine and it is perfect. The dimensions shoulb be between 9c x 11,5 cm and 12cm x 8 cm

```html
<!DOCTYPE html>
<html lang="en">
<head>
<meta charset="utf-8">
<title>Kemora — Red Wine Label</title>
<link rel="stylesheet" href="https://fonts.googleapis.com/css2?family=Cormorant+Garamond:wght@500;600&display=swap">
<style>
  :root {
    --backdrop: #2b2b2b;
    --label-paper: #f4f4f2;
    --label-band: #1b1b1c;
    --label-ink: #ebebea;
    --emblem-dark: #2a2a2a;
    --emblem-mid: #6a6a6a;
  }
  html, body {
    margin: 0;
    padding: 0;
    width: 1200px;
    height: 859px;
    overflow: hidden;
    background: var(--backdrop);
  }
  .stage {
    position: relative;
    width: 1200px;
    height: 859px;
  }
  .wine-label {
    position: absolute;
    left: 334px;
    top: 89px;
    width: 532px;
    height: 680px;
    box-shadow: 0 10px 30px rgba(0, 0, 0, 0.35);
  }
  .label-top {
    position: absolute;
    inset: 0 0 auto 0;
    height: 364px;
    background: var(--label-paper);
  }
  .emblem {
    position: absolute;
    left: 176px;
    top: 170px;
    width: 180px;
    height: 150px;
    border-radius: 50%;
    background: radial-gradient(ellipse at center, var(--emblem-dark) 0%, var(--emblem-dark) 35%, var(--emblem-mid) 60%, var(--label-paper) 72%);
  }
  .label-band {
    position: absolute;
    inset: 364px 0 0 0;
    background: var(--label-band);
    color: var(--label-ink);
    text-align: center;
  }
  .wine-name {
    position: absolute;
    left: 0;
    right: 0;
    top: 88px;
    margin: 0;
    font-family: "Cormorant Garamond", "Times New Roman", serif;
    font-weight: 600;
    font-size: 112px;
    line-height: 1;
    letter-spacing: 3px;
    text-transform: uppercase;
  }
  .wine-type {
    position: absolute;
    left: 0;
    right: 0;
    bottom: 26px;
    margin: 0;
    font-family: "Cormorant Garamond", "Times New Roman", serif;
    font-weight: 500;
    font-size: 22px;
    letter-spacing: 1px;
    text-transform: uppercase;
  }
</style>
</head>
<body>
  <main class="stage">
    <article class="wine-label">
      <section class="label-top">
        <div class="emblem" role="img" aria-label="Spinning top emblem with motion rings"></div>
      </section>
      <section class="label-band">
        <h1 class="wine-name">Kemora</h1>
        <p class="wine-type">Red Wine</p>
      </section>
    </article>
  </main>
</body>
</html>
```